Brell Stone Company Business Cards

Front and Back Business Card - logo and text setup - cool design. I need workable photoshop or illustrator files so I can setup each employee card with design that is created
Updates

Hi everyone, thank you for the great entries. Please no more white and blue cards - there are so many already - black and silver only now please. thanks!

Target Market(s)

Construction Industry - Facility Managers

Industry/Entity Type

Construction

Contact Information for Business Card

I really like contemporary simplistic looks - clean neat....not opposed to seeing some black backrounds

Requirements
Must have
• Logo/website address with design on front only - www.brellstone-example.com (logo attached)
• Back:
• Name/Title/Company Address/Phone/email address
Nice to have
• Cool design
Should not have
• Nothing gimmicky like Fire or Water - since we are a Fire Protection company - it has all been done

```html
<!DOCTYPE html>
<html lang="en">
<head>
<meta charset="utf-8">
<title>Brell Stone Company – Business Cards</title>
<link rel="stylesheet" href="https://fonts.googleapis.com/css2?family=Source+Sans+3:ital,wght@0,400;0,900;1,700&display=swap">
<style>
  :root {
    --blue: #0323a0;
    --red: #ff2020;
    --black: #000000;
    --white: #ffffff;
    --backdrop: #d4d7da;
    --card-w: 873px;
    --card-h: 499px;
    --radius: 34px;
  }
  * { margin: 0; padding: 0; box-sizing: border-box; }
  html, body { width: 1200px; height: 1193px; overflow: hidden; }
  body {
    background: var(--backdrop);
    position: relative;
    font-family: "Source Sans 3", "Myriad Pro", sans-serif;
    color: var(--white);
  }
  .card {
    position: absolute;
    width: var(--card-w);
    height: var(--card-h);
    border-radius: var(--radius);
    overflow: hidden;
  }
  .card--front { left: 52px; top: 81px; background: var(--black); }
  .card--back { left: 283px; top: 633px; background: var(--blue); }

  .card__waves { position: absolute; inset: 0; width: 100%; height: 100%; }

  .wordmark {
    position: absolute;
    left: 0; right: 0;
    text-align: center;
    font-weight: 900;
    letter-spacing: -0.02em;
    line-height: 1;
  }
  .card--front .wordmark { top: 62px; font-size: 104px; color: var(--red); }
  .card--back .wordmark { top: 160px; font-size: 118px; color: var(--white); }

  .person {
    position: absolute;
    left: 0; right: 0; top: 232px;
    text-align: center;
    font-style: italic;
    font-weight: 700;
  }
  .person__name { font-size: 34px; line-height: 40px; }
  .person__title { font-size: 29px; line-height: 36px; }

  .contact {
    position: absolute;
    left: 0; right: 0; top: 398px;
    text-align: center;
    font-weight: 400;
  }
  .contact__address { font-size: 23px; line-height: 30px; }
  .contact__row {
    margin-top: 9px;
    display: flex;
    justify-content: center;
    align-items: center;
    gap: 16px;
    font-size: 21px;
    line-height: 28px;
  }
  .contact__item { display: flex; align-items: center; gap: 7px; }
  .contact__icon { width: 20px; height: 20px; fill: none; stroke: var(--white); stroke-width: 1.6; }
  .contact__icon--solid { fill: var(--white); stroke: none; }

  .website {
    position: absolute;
    left: 0; right: 0; top: 328px;
    text-align: center;
    font-size: 28px;
    letter-spacing: 0.28em;
    font-weight: 400;
  }
</style>
</head>
<body>

<section class="card card--front">
  <svg class="card__waves" viewBox="0 0 873 499" preserveAspectRatio="none" aria-hidden="true">
    <path d="M0,272 Q440,470 873,276 L873,499 L0,499 Z" fill="var(--blue)"/>
    <path d="M0,224 Q380,405 710,330 Q380,415 0,260 Z" fill="var(--red)"/>
  </svg>
  <div class="wordmark">Brell Stone</div>
  <div class="person">
    <p class="person__name">Dana Whitcomb</p>
    <p class="person__title">President</p>
  </div>
  <div class="contact">
    <p class="contact__address">48 Harbor Park Road, Millbrook, NY 12545</p>
    <div class="contact__row">
      <span class="contact__item">
        <svg class="contact__icon contact__icon--solid" viewBox="0 0 24 24" aria-hidden="true"><path d="M6.6 10.8a15 15 0 0 0 6.6 6.6l2.2-2.2a1 1 0 0 1 1-.25 11.4 11.4 0 0 0 3.6.57 1 1 0 0 1 1 1V20a1 1 0 0 1-1 1A17 17 0 0 1 3 4a1 1 0 0 1 1-1h3.5a1 1 0 0 1 1 1c0 1.25.2 2.45.57 3.6a1 1 0 0 1-.25 1z"/></svg>
        (555) 014-2287
      </span>
      <span class="contact__item">
        <svg class="contact__icon contact__icon--solid" viewBox="0 0 24 24" aria-hidden="true"><path d="M2 5h20v14H2z M4 7l8 6 8-6" fill="var(--white)" stroke="var(--blue)" stroke-width="1.6"/></svg>
        info@brellstone-example.com
      </span>
      <span class="contact__item">
        <svg class="contact__icon" viewBox="0 0 24 24" aria-hidden="true"><circle cx="12" cy="12" r="9.5"/><ellipse cx="12" cy="12" rx="4" ry="9.5"/><path d="M2.5 12h19M4 7h16M4 17h16"/></svg>
        www.brellstone-example.com
      </span>
    </div>
  </div>
</section>

<section class="card card--back">
  <div class="wordmark">Brell Stone</div>
  <p class="website">www.brellstone-example.com</p>
</section>

</body>
</html>
```